Redesign of Form/Document Navigation Page

I need a redesign of our document and navigation bar on the left. We want the same navigation bar layout/setup but want the buttons and typography to be simple and matching all over. The form needs to be aesthetically pleasing and fit within the page.

1st attachment is our Direct Deposit and the second is the form continued.

```html
<!DOCTYPE html>
<html lang="en">
<head>
<meta charset="utf-8">
<title>Direct Deposit Authorization</title>
<link href="https://fonts.googleapis.com/css2?family=Open+Sans:wght@400;600;700&family=Roboto:wght@400&display=swap" rel="stylesheet">
<style>
:root{
  --blue:#1d5aa3;
  --blue-dark:#174b8a;
  --orange:#f5a818;
  --text:#333;
  --muted:#555;
  --line:#bfbfbf;
  --page:#eceef1;
  --footer:#1f1f1f;
  --white:#fff;
}
*{box-sizing:border-box;margin:0;padding:0}
html,body{width:1200px;height:868px;overflow:hidden}
body{font-family:"Open Sans",sans-serif;color:var(--text);background:var(--page);position:relative}
.site-header{position:absolute;left:0;top:0;width:1200px;height:99px;background:var(--white)}
.brand{position:absolute;left:92px;top:30px;display:flex;align-items:center;gap:8px}
.brand-dot{width:34px;height:34px;border-radius:50%;background:var(--blue)}
.brand-name{font-weight:700;font-size:19px;color:var(--orange);line-height:1;text-transform:uppercase;width:190px}
.main-nav{position:absolute;left:427px;top:39px;display:flex;gap:30px;font-size:17px;color:#222}
.user{position:absolute;left:853px;top:40px;font-size:15px;color:#222;display:flex;align-items:center;gap:8px}
.btn-profile{position:absolute;left:992px;top:35px;width:122px;height:28px;background:var(--blue);color:var(--white);font-size:11.5px;display:flex;align-items:center;justify-content:center;border:1px solid var(--blue-dark)}
.side-nav{position:absolute;left:87px;top:131px;width:273px}
.side-item{position:absolute;left:0;width:273px;height:83px;background:var(--white);border:1px solid var(--line);display:flex;align-items:center;padding-left:20px;gap:14px;color:var(--blue);font-size:15px}
.side-item svg{width:34px;height:34px;flex:none}
.panel{position:absolute;left:374px;top:129px;width:740px;height:629px;background:var(--white);border:1px solid var(--line)}
.scroll-track{position:absolute;right:0;top:0;width:13px;height:100%;background:#f1f1f1}
.scroll-thumb{position:absolute;right:0;top:321px;width:13px;height:89px;background:#9a9a9a}
.panel h1{position:absolute;left:20px;top:30px;font-size:17.5px;font-weight:400;color:var(--blue)}
.terms{position:absolute;left:21px;top:60px;width:680px;font-size:10px;line-height:17px;color:var(--muted)}
.terms p+p{margin-top:8px}
.form-box{position:absolute;left:20px;width:671px;background:var(--white);border:1px solid #cfcfcf;box-shadow:0 1px 3px rgba(0,0,0,.08)}
.field-label{position:absolute;font-size:11.5px;color:#333}
.input{position:absolute;height:29px;border:1px solid #aaa;background:var(--white)}
.btn{position:absolute;height:27px;background:var(--orange);color:var(--white);font-size:11.5px;font-weight:600;display:flex;align-items:center;justify-content:center}
.form-box h2{position:absolute;left:30px;top:24px;font-size:17.5px;font-weight:400;color:var(--blue)}
.site-footer{position:absolute;left:0;top:794px;width:1200px;height:74px;background:var(--footer);color:#aaa;font-family:"Roboto",sans-serif}
.copyright{position:absolute;left:86px;top:28px;font-size:14px}
.social{position:absolute;left:992px;top:22px;display:flex;gap:3px}
.social span{width:28px;height:28px;border:2px solid #ddd;border-radius:50%}
</style>
</head>
<body>
<header class="site-header">
  <div class="brand"><span class="brand-dot"></span><span class="brand-name">Sentinel Watch Services</span></div>
  <nav class="main-nav"><span>HOME</span><span>HELP</span></nav>
  <div class="user">DANA MORROW
    <svg width="17" height="17" viewBox="0 0 24 24" fill="none" stroke="#555" stroke-width="3" stroke-linecap="round"><path d="M12 2v9"/><path d="M6.3 6a8 8 0 1 0 11.4 0"/></svg>
  </div>
  <a class="btn-profile">BACK TO PROFILE</a>
</header>

<nav class="side-nav">
  <div class="side-item" style="top:0">
    <svg viewBox="0 0 34 34"><circle cx="17" cy="17" r="16" fill="var(--blue)"/><text x="17" y="24" text-anchor="middle" font-size="20" font-weight="700" fill="#fff" font-family="Open Sans,sans-serif">$</text></svg>DIRECT DEPOSIT</div>
  <div class="side-item" style="top:89px">
    <svg viewBox="0 0 34 34" fill="none" stroke="var(--blue)" stroke-width="2.5"><rect x="2" y="4" width="30" height="22"/><path d="M8 11h18M8 16h10"/><circle cx="24" cy="25" r="4" fill="var(--blue)"/></svg>CHANGE W-4</div>
  <div class="side-item" style="top:180px">
    <svg viewBox="0 0 34 34" fill="none" stroke="var(--blue)" stroke-width="3.5" stroke-linecap="round"><path d="M6 28L26 8M8 6l20 22M4 10l6-6"/></svg>LABOUR CODE</div>
  <div class="side-item" style="top:271px">
    <svg viewBox="0 0 34 34" fill="none" stroke="var(--blue)" stroke-width="2.5"><circle cx="17" cy="17" r="15"/><path d="M17 15v10" stroke-width="3.5"/><circle cx="17.5" cy="10" r="1.5" fill="var(--blue)"/></svg>PERSONAL INFORMATION</div>
  <div class="side-item" style="top:362px">
    <svg viewBox="0 0 34 34"><rect x="2" y="8" width="30" height="22" fill="var(--blue)"/><rect x="12" y="4" width="10" height="5" fill="none" stroke="var(--blue)" stroke-width="2.5"/><path d="M17 15v10M12 20h10" stroke="#fff" stroke-width="2.5"/></svg>APPRASIAL &amp; REVIEW</div>
  <div class="side-item" style="top:452px">
    <svg viewBox="0 0 34 34" fill="none" stroke="var(--blue)" stroke-width="2.5"><rect x="5" y="3" width="22" height="28"/><path d="M10 10h12M10 15h12M10 20h12M10 25h8"/></svg>WRITE UP-SLIP</div>
  <div class="side-item" style="top:544px">
    <svg viewBox="0 0 34 34"><rect x="3" y="6" width="22" height="26" fill="var(--blue)"/><rect x="9" y="3" width="10" height="6" fill="#fff" stroke="var(--blue)" stroke-width="2.5"/><path d="M8 16h10M8 22h8" stroke="#fff" stroke-width="2.5"/><path d="M18 27L31 12" stroke="var(--blue)" stroke-width="3.5"/></svg>EMPLOYEE PERFORMANCE</div>
</nav>

<main class="panel">
  <div class="scroll-track"><div class="scroll-thumb"></div></div>
  <h1>IMPORTANT! PLEASE READ AND SIGN BEFORE COMPLETING AND SUBMITTING</h1>
  <div class="terms">
    <p>I hereby authorize SENTINEL WATCH SERVICES to deposit any amounts owed me, as instructed by my employer, by initiating credit entries to ow account at the financial institution (hereinafter "Bank") indicated on this form. Further. I authorize Bank to accept and to credit any credit entries indicated by SENTINEL WATCH SERVICES to my account. In the even that SENTINEL WATCH SERVICES deposits funds erroneously</p>
    <p>This authorization is to remain in full force and effect until SENTINEL WATCH SERVICES and Bank have received written notice from me of its termination in such time and in such manner as to afford SENTINEL WATCH SERVICES and Bank reasonable opportunity to act on it.</p>
  </div>

  <section class="form-box" style="top:176px;height:130px">
    <span class="field-label" style="left:33px;top:25px">Employee Name</span>
    <span class="field-label" style="left:239px;top:25px">Employee Signature</span>
    <span class="field-label" style="left:444px;top:25px">Sign date</span>
    <div class="input" style="left:33px;top:42px;width:184px"></div>
    <div class="input" style="left:239px;top:42px;width:184px"></div>
    <div class="input" style="left:444px;top:42px;width:184px"></div>
    <a class="btn" style="left:32px;top:82px;width:139px">ACCEPT DOCUMENT</a>
  </section>

  <section class="form-box" style="top:322px;height:265px">
    <h2>ONLY PAYROLL MANAGER SIGNS BELOW</h2>
    <span class="field-label" style="left:33px;top:65px">Company Name</span>
    <span class="field-label" style="left:353px;top:65px">Employee File Number</span>
    <div class="input" style="left:33px;top:85px;width:279px"></div>
    <div class="input" style="left:344px;top:85px;width:279px"></div>
    <span class="field-label" style="left:32px;top:129px">Comments</span>
    <div class="input" style="left:32px;top:148px;width:591px;height:44px"></div>
    <a class="btn" style="left:32px;top:212px;width:94px">SEND NOW</a>
  </section>
</main>

<footer class="site-footer">
  <p class="copyright">© 2016 Company Name&nbsp; All right reserved&nbsp; Term of Use</p>
  <div class="social"><span></span><span></span><span></span><span></span></div>
</footer>
</body>
</html>
```